Web design required

1-We need a web design for existing company based in New Zealand
2-We build residential house and light commercial
3-We has in-house designer which allow us can provide interior design
4-We modeling project before site construction, which enable both client and construction team to visually analysis whole project,

Target Market(s)

middle class residential house market
Ref: http://www.parvellbuilders.co.nz/

Industry/Entity Type

Construction Company

Number of Pages Required

1 page

Font styles to use
Sans Serif
Other font styles liked:
• Such as : Central Gothic or similar which has more design taste

Colors

Designer to choose colors to be used in the design.

Requirements
Must have
• Front sheet, contact information, sample project

```html
<!DOCTYPE html>
<html lang="en">
<head>
<meta charset="utf-8">
<title>Kestrel Homes</title>
<link href="https://fonts.googleapis.com/css2?family=Open+Sans:wght@400;600;700&family=Roboto:wght@400;500;700&display=swap" rel="stylesheet">
<style>
:root{
  --blue:#0b4ea2;
  --blue-dark:#083d80;
  --ink:#222;
  --text:#666;
  --muted:#888;
  --light:#f4f4f4;
  --dark:#262626;
  --white:#fff;
}
*{box-sizing:border-box;margin:0;padding:0}
html,body{width:1200px;height:3273px;overflow:hidden}
body{position:relative;background:var(--white);font-family:"Open Sans",Arial,sans-serif;color:var(--ink)}
.abs{position:absolute}
a{color:inherit;text-decoration:none}

/* header */
.site-header{position:absolute;left:0;top:0;width:1200px;height:131px;background:var(--white)}
.brand{position:absolute;left:98px;top:38px;display:flex;align-items:center;gap:12px;font-family:"Roboto",sans-serif;font-weight:500;font-size:26px;color:var(--blue);letter-spacing:.5px;white-space:nowrap}
.brand-dot{width:36px;height:36px;background:var(--blue);border-radius:50%;flex:none}
.top-contact{position:absolute;top:22px;right:98px;display:flex;gap:26px;font-size:15px;color:#333}
.top-contact span{display:flex;align-items:center;gap:10px}
.top-contact i{width:30px;height:30px;border-radius:50%;background:var(--blue);display:flex;align-items:center;justify-content:center}
.top-contact i.dark{background:#333}
.main-nav{position:absolute;left:419px;top:74px;width:781px;height:57px;background:var(--blue);clip-path:polygon(30px 0,100% 0,100% 100%,0 100%)}
.main-nav ul{list-style:none;display:flex;height:100%;align-items:center;padding-left:66px}
.main-nav li{font-family:"Roboto",sans-serif;font-weight:500;font-size:15px;color:var(--white);width:128px}

/* hero */
.hero{position:absolute;left:0;top:131px;width:1200px;height:541px;background:linear-gradient(135deg,#3a2a20 0%,#6a5141 40%,#4a3a2e 70%,#2b211b 100%)}
.hero-shade{position:absolute;inset:0;background:rgba(0,0,0,.35)}
.hero h1{position:absolute;top:112px;width:100%;text-align:center;font-weight:700;font-size:56px;color:var(--white);letter-spacing:1px}
.hero p{position:absolute;top:206px;left:190px;width:820px;text-align:center;font-size:15px;line-height:36px;color:var(--white);font-weight:600}
.hero .btn{position:absolute;left:535px;top:305px;width:130px;height:53px;background:var(--blue);border:2px solid rgba(255,255,255,.6);color:var(--white);font-size:15px;display:flex;align-items:center;justify-content:center}
.hero .arrow{position:absolute;top:240px}

/* feature cards */
.features{position:absolute;left:98px;top:576px;width:1004px;height:410px;display:flex}
.feature{width:334.6px;height:410px;background:var(--blue);padding:22px 18px;color:var(--white)}
.feature.alt{background:var(--dark)}
.feature h3{font-family:"Roboto",sans-serif;font-weight:500;font-size:20px;margin-bottom:14px;white-space:nowrap}
.feature p{font-size:12.5px;line-height:22px;opacity:.9}
.feature .photo{margin-top:12px;height:242px;border:3px solid var(--white)}
.features-shadow{position:absolute;left:98px;top:982px;width:1004px;height:30px;background:radial-gradient(ellipse at 50% 0,rgba(0,0,0,.22),transparent 70%)}

/* about */
.section-title{position:absolute;width:100%;text-align:center;font-family:"Roboto",sans-serif;font-weight:700;font-size:27px;color:var(--blue);letter-spacing:.5px}
.about-text{position:absolute;left:150px;top:1130px;width:900px;text-align:center;font-size:13.5px;line-height:24px;color:var(--text)}
.stats{position:absolute;left:60px;top:1255px;width:1080px;display:flex}
.stat{width:216px;text-align:center;border-right:1px solid #ddd;height:120px}
.stat:last-child{border-right:none}
.stat svg{display:block;margin:0 auto 16px}
.stat .label{font-family:"Roboto",sans-serif;font-size:14px;color:var(--blue);text-transform:uppercase}
.stat .label.dark{color:#333}
.stat .value{font-family:"Roboto",sans-serif;font-size:19px;font-weight:500;color:var(--blue);margin-top:10px}
.stat .value.dark{color:#333}

/* services */
.services{position:absolute;left:0;top:1451px;width:1200px;height:530px;background:var(--light)}
.services-photo{position:absolute;left:0;top:0;width:563px;height:530px;background:linear-gradient(180deg,#b8c8dc 0%,#e4e8ee 30%,#8a8d90 60%,#4a4b4c 100%)}
.services h2{position:absolute;left:626px;top:42px;font-family:"Roboto",sans-serif;font-weight:700;font-size:26px;color:var(--blue)}
.underline{position:absolute;height:3px;background:var(--blue)}
.services .intro{position:absolute;left:626px;top:108px;width:480px;font-size:13.5px;line-height:26px;color:var(--muted)}
.service{position:absolute;width:240px}
.service h4{font-family:"Roboto",sans-serif;font-weight:500;font-size:15px;color:#333;margin:10px 0 6px}
.service p{font-size:12.5px;line-height:22px;color:var(--muted)}

/* projects */
.project{position:absolute;width:321px;height:288px;border:1px solid #ddd;background:var(--white)}
.project .photo{height:230px}
.project .name{height:56px;display:flex;align-items:center;justify-content:center;font-family:"Roboto",sans-serif;font-weight:500;font-size:19px;color:#333;border-top:1px solid #ddd;white-space:nowrap}

/* footer */
.site-footer{position:absolute;left:0;top:2852px;width:1200px;height:421px;background:linear-gradient(135deg,#2b2b2b,#1f1f1f)}
.site-footer .brand{left:98px;top:176px;color:var(--white);font-size:23px}
.site-footer .brand-dot{background:var(--white);width:30px;height:30px}
.f-head{position:absolute;font-family:"Roboto",sans-serif;font-weight:500;font-size:16px;color:var(--white);letter-spacing:.5px}
.f-line{position:absolute;height:2px;background:var(--white);width:95px}
.links{position:absolute;left:364px;top:125px;list-style:none}
.links li{font-size:14px;color:var(--white);line-height:31px}
.links li::before{content:">";margin-right:12px}
.contact-item{position:absolute;left:554px;width:240px;display:flex;gap:16px}
.contact-item .ic{width:38px;height:38px;border-radius:50%;border:2px solid #888;display:flex;align-items:center;justify-content:center;flex:none}
.contact-item b{display:block;font-family:"Roboto",sans-serif;font-weight:500;font-size:14px;color:var(--white);margin-bottom:3px}
.contact-item span{display:block;font-size:12.5px;color:#bbb;line-height:19px;white-space:nowrap}
.field{position:absolute;border:1px solid #ccc;font-size:11px;color:#ccc;padding:8px 10px}
.send{position:absolute;left:814px;top:241px;width:120px;height:40px;background:var(--blue);border:2px solid #ddd;color:var(--white);font-size:11px;display:flex;align-items:center;justify-content:center}
.copy-rule{position:absolute;left:364px;top:355px;width:738px;height:1px;background:#555}
.copyright{position:absolute;top:378px;width:100%;text-align:center;font-size:14px;color:var(--white);font-weight:600}
</style>
</head>
<body>

<header class="site-header">
  <div class="brand"><span class="brand-dot"></span>KESTREL HOMES</div>
  <div class="top-contact">
    <span><i><svg width="14" height="11" viewBox="0 0 14 11"><rect x="0.5" y="0.5" width="13" height="10" fill="none" stroke="#fff"/><path d="M0.5 0.5 L7 6 L13.5 0.5" fill="none" stroke="#fff"/></svg></i>info@kestrelhomes.co.nz</span>
    <span><i class="dark"><svg width="14" height="14" viewBox="0 0 14 14"><path d="M3 1 L5 4 L4 5.5 Q5.5 8.5 8.5 10 L10 9 L13 11 L11.5 13 Q5 12.5 1 3 Z" fill="#fff"/></svg></i>0064 9 300 4821</span>
  </div>
  <nav class="main-nav"><ul><li>HOME</li><li>SERVICES</li><li>ABOUT</li><li>PROJECTS</li><li>CONTACT US</li></ul></nav>
</header>

<section class="hero">
  <div class="abs" role="img" aria-label="Photo of a modern living room interior with sofa and timber ceiling" style="inset:0"></div>
  <div class="hero-shade"></div>
  <h1>KESTREL HOMES</h1>
  <p>"Kestrel Homes is dedicated to creating and renovating beautiful and unusual buildings. Kestrel Homes works with you to take dream houses off the blueprints and into reality."</p>
  <a class="btn" href="#">READ MORE</a>
  <svg class="arrow" style="left:34px" width="30" height="60" viewBox="0 0 30 60"><path d="M26 2 L4 30 L26 58" fill="none" stroke="#fff" stroke-width="2"/></svg>
  <svg class="arrow" style="right:34px" width="30" height="60" viewBox="0 0 30 60"><path d="M4 2 L26 30 L4 58" fill="none" stroke="#fff" stroke-width="2"/></svg>
</section>

<div class="features-shadow"></div>
<div class="features">
  <article class="feature">
    <h3>Preconstruction Planning</h3>
    <p>Kestrel Homes works with you to take dream houses off the blueprints and into reality. We have the knowledge.</p>
    <div class="photo" role="img" aria-label="Photo of a house under construction wrapped in scaffolding" style="background:linear-gradient(180deg,#9fb6cc,#d9dde2 50%,#6f7a72)"></div>
  </article>
  <article class="feature alt">
    <h3>Construction Modelling</h3>
    <p>Kestrel Homes works with you to take dream houses off the blueprints and into reality. We have the knowledge.</p>
    <div class="photo" role="img" aria-label="Photo of a new two-storey white weatherboard house" style="background:linear-gradient(180deg,#6f9ad0,#e8e8e6 50%,#7b7466)"></div>
  </article>
  <article class="feature">
    <h3>Full Project Management</h3>
    <p>Kestrel Homes works with you to take dream houses off the blueprints and into reality. We have the knowledge.</p>
    <div class="photo" role="img" aria-label="Photo of an interior with a timber-lined ceiling" style="background:linear-gradient(160deg,#a0673a,#d9b08a 40%,#eae6e0 70%,#bdb7ae)"></div>
  </article>
</div>

<h2 class="section-title" style="top:1080px">ABOUT KESTREL HOMES</h2>
<p class="about-text">Kestrel Homes is dedicated to creating and renovating beautiful and unusual buildings. Kestrel Homes works with you to take dream houses off the blueprints and into reality. We have the knowledge and expertise to customise homes to suit you – from unusual materials and designs to environmentally sensitive locations.</p>

<div class="stats">
  <div class="stat">
    <svg width="44" height="36" viewBox="0 0 44 36"><rect x="4" y="2" width="36" height="14" rx="2" fill="none" stroke="#0b4ea2" stroke-width="3"/><rect x="2" y="16" width="40" height="12" fill="#0b4ea2"/><rect x="3" y="28" width="4" height="6" fill="#0b4ea2"/><rect x="37" y="28" width="4" height="6" fill="#0b4ea2"/></svg>
    <div class="label">Bedrooms</div><div class="value">3</div>
  </div>
  <div class="stat">
    <svg width="44" height="40" viewBox="0 0 44 40"><path d="M4 2 V38 H42" fill="none" stroke="#333" stroke-width="2"/><path d="M10 8 H32 V32 H10 Z M10 16 H32 M10 24 H32 M18 8 V32 M25 8 V32" fill="none" stroke="#333" stroke-width="1.5"/><path d="M32 32 L40 24 V32 Z" fill="#333"/></svg>
    <div class="label dark">Square Feet</div><div class="value dark">2520</div>
  </div>
  <div class="stat">
    <svg width="44" height="38" viewBox="0 0 44 38"><path d="M8 18 V6 Q8 2 12 2 Q16 2 16 6" fill="none" stroke="#0b4ea2" stroke-width="2.5"/><path d="M2 18 H42 V24 Q42 32 32 32 H12 Q2 32 2 24 Z" fill="#0b4ea2"/><rect x="8" y="32" width="3" height="5" fill="#0b4ea2"/><rect x="33" y="32" width="3" height="5" fill="#0b4ea2"/></svg>
    <div class="label">Baths</div><div class="value">2</div>
  </div>
  <div class="stat">
    <svg width="40" height="40" viewBox="0 0 40 40"><rect x="2" y="6" width="36" height="32" rx="2" fill="none" stroke="#333" stroke-width="2.5"/><rect x="2" y="6" width="36" height="8" fill="#333"/><rect x="10" y="1" width="3" height="8" fill="#333"/><rect x="27" y="1" width="3" height="8" fill="#333"/><g fill="#333"><rect x="8" y="18" width="5" height="4"/><rect x="17" y="18" width="5" height="4"/><rect x="26" y="18" width="5" height="4"/><rect x="8" y="26" width="5" height="4"/><rect x="17" y="26" width="5" height="4"/><rect x="26" y="26" width="5" height="4"/></g></svg>
    <div class="label dark">Year Build</div><div class="value dark">2016</div>
  </div>
  <div class="stat">
    <svg width="40" height="38" viewBox="0 0 40 38"><path d="M2 14 L20 2 L38 14" fill="none" stroke="#0b4ea2" stroke-width="3"/><path d="M8 22 L12 15 H28 L32 22 H34 V32 H6 V22 Z" fill="#0b4ea2"/><circle cx="12" cy="33" r="3" fill="#0b4ea2"/><circle cx="28" cy="33" r="3" fill="#0b4ea2"/></svg>
    <div class="label">Car Parking</div><div class="value">1</div>
  </div>
</div>

<section class="services">
  <div class="services-photo" role="img" aria-label="Photo of a two-storey building wrapped in scaffolding with a work van parked in front"></div>
  <h2>OUR SERVICES</h2>
  <div class="underline" style="left:626px;top:84px;width:190px"></div>
  <p class="intro">Kestrel Homes works with you to take dream houses off the blueprints and into reality.</p>

  <div class="service" style="left:626px;top:186px">
    <svg width="44" height="46" viewBox="0 0 44 46"><path d="M16 2 H28 L24 10 H20 Z" fill="#0b4ea2"/><path d="M18 12 H26 Q40 22 38 34 Q36 42 22 42 Q8 42 6 34 Q4 22 18 12 Z" fill="#0b4ea2"/><text x="22" y="34" text-anchor="middle" font-family="Roboto,sans-serif" font-size="14" font-weight="700" fill="#fff">$</text><rect x="2" y="43" width="40" height="3" fill="#0b4ea2"/></svg>
    <h4>Residential House</h4>
    <p>Kestrel Homes is dedicated to creating and renovating beautiful.</p>
  </div>
  <div class="service" style="left:884px;top:186px">
    <svg width="48" height="46" viewBox="0 0 48 46"><g fill="#0b4ea2"><rect x="4" y="34" width="6" height="10"/><rect x="14" y="28" width="6" height="16"/><rect x="24" y="22" width="6" height="22"/><rect x="34" y="14" width="6" height="30"/></g><path d="M2 26 L16 16 L24 20 L42 4" fill="none" stroke="#0b4ea2" stroke-width="3"/><path d="M36 2 H45 V11" fill="none" stroke="#0b4ea2" stroke-width="3"/></svg>
    <h4>Light Commercial</h4>
    <p>Kestrel Homes is dedicated to creating and renovating beautiful.</p>
  </div>
  <div class="service" style="left:626px;top:350px">
    <svg width="48" height="44" viewBox="0 0 48 44"><path d="M4 20 L24 4 L44 20" fill="none" stroke="#0b4ea2" stroke-width="3"/><rect x="2" y="20" width="44" height="22" fill="none" stroke="#0b4ea2" stroke-width="3"/><rect x="10" y="26" width="12" height="10" fill="#0b4ea2"/><rect x="28" y="26" width="10" height="16" fill="#0b4ea2"/></svg>
    <h4>Model Project</h4>
    <p>Kestrel Homes is dedicated to creating and renovating beautiful.</p>
  </div>
  <div class="service" style="left:884px;top:350px">
    <svg width="44" height="46" viewBox="0 0 44 46"><path d="M4 18 L22 4 L40 18 V44 H4 Z" fill="none" stroke="#0b4ea2" stroke-width="3"/><circle cx="22" cy="28" r="8" fill="none" stroke="#0b4ea2" stroke-width="3"/><circle cx="22" cy="28" r="3" fill="#0b4ea2"/><g stroke="#0b4ea2" stroke-width="3"><path d="M22 16 V19 M22 37 V40 M10 28 H13 M31 28 H34"/></g></svg>
    <h4>Construction Team</h4>
    <p>Kestrel Homes is dedicated to creating and renovating beautiful.</p>
  </div>
</section>

<h2 class="section-title" style="top:2048px">OUR PROJECTS</h2>
<div class="underline" style="left:565px;top:2101px;width:70px"></div>

<article class="project" style="left:98px;top:2164px">
  <div class="photo" role="img" aria-label="Photo of a house under construction in scaffolding" style="background:linear-gradient(180deg,#8fb0d2,#dfe3e8 50%,#707a70)"></div>
  <div class="name">Ashford Project</div>
</article>
<article class="project" style="left:441px;top:2164px">
  <div class="photo" role="img" aria-label="Photo of a new white two-storey house" style="background:linear-gradient(180deg,#6a98d0,#e7e7e5 55%,#7a7263)"></div>
  <div class="name">Whitmore Project</div>
</article>
<article class="project" style="left:781px;top:2164px">
  <div class="photo" role="img" aria-label="Photo of a new white two-storey house" style="background:linear-gradient(180deg,#6a98d0,#e7e7e5 55%,#7a7263)"></div>
  <div class="name">Kowhai Bay Project - Interior</div>
</article>
<article class="project" style="left:98px;top:2485px">
  <div class="photo" role="img" aria-label="Photo collage of a dark modern house with glass balcony" style="background:linear-gradient(160deg,#c9cfd6,#4a4d50 50%,#2a2c2e)"></div>
  <div class="name">Kowhai Bay Project</div>
</article>
<article class="project" style="left:441px;top:2485px">
  <div class="photo" role="img" aria-label="Photo of a white house behind a garden wall with palm trees" style="background:linear-gradient(180deg,#2a3a2a,#e8e8e6 55%,#3a3a3a)"></div>
  <div class="name">Elmsley Project</div>
</article>
<article class="project" style="left:781px;top:2485px">
  <div class="photo" role="img" aria-label="Photo of a modern house with lit windows and a garage at dusk" style="background:linear-gradient(180deg,#3d6fb8,#9eb4d4 45%,#d8c8a8 65%,#6a6a6a)"></div>
  <div class="name">Rimu Lane Project</div>
</article>

<footer class="site-footer">
  <div class="brand"><span class="brand-dot"></span>KESTREL HOMES</div>

  <div class="f-head" style="left:364px;top:72px">USEFUL LINKS</div>
  <div class="f-line" style="left:364px;top:100px"></div>
  <ul class="links"><li>Home</li><li>Services</li><li>About</li><li>Projects</li><li>Contact Us</li></ul>

  <div class="f-head" style="left:554px;top:72px">CONTACT US</div>
  <div class="contact-item" style="top:128px">
    <div class="ic"><svg width="12" height="16" viewBox="0 0 12 16"><path d="M6 16 Q0 8 0 6 A6 6 0 0 1 12 6 Q12 8 6 16 Z" fill="#fff"/><circle cx="6" cy="6" r="2" fill="#262626"/></svg></div>
    <div><b>ADDRESS,</b><span>48 Harbour View Rd, Unit 3,</span><span>NZ</span></div>
  </div>
  <div class="contact-item" style="top:208px">
    <div class="ic"><svg width="10" height="16" viewBox="0 0 10 16"><rect x="1" y="1" width="8" height="14" rx="1.5" fill="none" stroke="#fff" stroke-width="1.5"/></svg></div>
    <div><b>PHONE NUMBER:</b><span>180 044 7190</span></div>
  </div>
  <div class="contact-item" style="top:270px">
    <div class="ic"><svg width="14" height="11" viewBox="0 0 14 11"><rect x="0.5" y="0.5" width="13" height="10" fill="#fff"/><path d="M0.5 0.5 L7 6 L13.5 0.5" fill="none" stroke="#262626"/></svg></div>
    <div><b>EMAIL:</b><span>hello@kestrelhomes.co.nz</span></div>
  </div>

  <div class="f-head" style="left:814px;top:68px">CONTACT FORM</div>
  <div class="field" style="left:814px;top:120px;width:138px;height:36px">Name</div>
  <div class="field" style="left:962px;top:120px;width:140px;height:36px">Phone</div>
  <div class="field" style="left:814px;top:166px;width:288px;height:62px">Message</div>
  <div class="send">SEND MESSAGE</div>

  <div class="copy-rule"></div>
  <div class="copyright">Copyrights @ 2017 Kestrel Homes. All Rights Reserved.</div>
</footer>

</body>
</html>
```